Dental Medical History Form - Content provided

Design a medical history form for a dental practice. Content is provided so all that is needed is the formatting to make it look great and easy to read.

"Patient Information" to include all information contained in top portion of the "Patient Medical History Form" docx file.

"Medical History" should follow the formatting and content of the "Exact Medical History" file as this is what the entry fields look like in our practice software and so we would like it to match.

1st page - Patient info, allergies, medications, antibiotics, joint replacement, pregnancy.

2nd page - Do you have, or have you had, any of the following? . . . . . . .
Updates

Target Market(s)

All ages but must be clear enough for elderly to read. Use as much space as possible to keep font size bigger yet keep to two pages

Industry/Entity Type

Dental

Font styles to use
Sans Serif

Requirements
Must have
• All content provided
• Our logo at the top (file provided)
• Century Gothic Font
• Limit to two pages

```html
<!DOCTYPE html>
<html lang="en">
<head>
<meta charset="utf-8">
<title>Harbourline Dental – Confidential Medical History</title>
<link rel="stylesheet" href="https://fonts.googleapis.com/css2?family=Didact+Gothic&family=PT+Sans+Narrow:wght@400;700&display=swap">
<style>
  :root{
    --bg:#e9e9e9;
    --paper:#ffffff;
    --ink:#33424d;
    --ink-soft:#5d6b75;
    --line:#8a969e;
    --band:#d6d9dc;
    --edge:#d0d0d0;
  }
  *{box-sizing:border-box;margin:0;padding:0}
  html,body{width:1200px;height:784px;overflow:hidden;background:var(--bg)}
  body{display:flex;align-items:center;justify-content:center;
    font-family:"PT Sans Narrow",Arial,sans-serif;color:var(--ink)}
  .form-sheet{position:relative;width:548px;height:766px;background:var(--paper);
    box-shadow:0 1px 0 var(--edge),0 3px 8px rgba(0,0,0,.08);padding:20px 30px 14px 30px;
    display:flex;flex-direction:column;font-size:10.5px}
  .edge-tab{position:absolute;width:8px;height:22px;background:var(--bg);border-radius:0 4px 4px 0;left:0}
  .edge-tab.right{left:auto;right:0;border-radius:4px 0 0 4px}
  .masthead{display:flex;justify-content:space-between;align-items:flex-start}
  .practice-name{font-family:"PT Sans Narrow",sans-serif;font-weight:700;font-size:22px;line-height:1;
    letter-spacing:1px;color:var(--ink);text-transform:uppercase;padding-top:4px}
  .contact{text-align:right;font-weight:700;font-size:9px;line-height:1.35}
  .contact .phone{font-size:12px}
  .form-title{font-family:"Didact Gothic",sans-serif;font-weight:700;text-align:center;
    letter-spacing:4px;font-size:15px;margin:10px 0 10px;-webkit-text-stroke:.5px var(--ink)}
  .row{display:flex;align-items:flex-end;gap:6px;margin-bottom:7px;white-space:nowrap}
  .label{flex:none}
  .field{flex:1;height:15px;border:1px solid var(--line)}
  .field.w120{flex:none;width:120px}
  .sub{font-size:9px;color:var(--ink-soft);display:flex;margin:0 0 2px 90px}
  .sub span{flex:1}
  .box{display:inline-block;width:10px;height:10px;border:1px solid var(--line);vertical-align:-1px;margin-left:3px}
  .section-band{font-weight:700;font-size:12px;text-align:center;padding:3px 0;margin:7px -30px 7px;
    background:linear-gradient(to bottom,#fff 0%,var(--band) 50%,#fff 100%)}
  .check-grid{display:grid;gap:6px 8px;margin-bottom:6px}
  .check-grid.allergy{grid-template-columns:repeat(8,auto)}
  .check-grid.meds{grid-template-columns:repeat(6,auto)}
  .check-grid span{white-space:nowrap}
  .write-line{border-bottom:1px solid var(--line);height:21px}
  .question{display:flex;justify-content:space-between;margin-top:8px}
  .question .answers span{margin-left:14px}
  .turnover{margin:12px auto 0;font-weight:700;font-size:12px;padding:3px 30px;
    background:linear-gradient(to bottom,#fff,var(--band),#fff)}
</style>
</head>
<body>
<main class="form-sheet">
  <span class="edge-tab" style="top:80px"></span>
  <span class="edge-tab right" style="top:80px"></span>
  <span class="edge-tab" style="bottom:26px"></span>

  <header class="masthead">
    <div class="practice-name">Harbourline Dental</div>
    <div class="contact">
      <div class="phone">(02) 5550 1234</div>
      <div>Harbourline Dental, Suite 4/88 Shoreline Rd,</div>
      <div>Bayview NSW 2999</div>
    </div>
  </header>

  <h1 class="form-title">CONFIDENTIAL MEDICAL HISTORY</h1>

  <div class="sub"><span>First</span><span>Middle</span><span>Last</span></div>
  <div class="row"><span class="label">Name:</span><span class="field"></span><span class="field"></span><span class="field"></span></div>
  <div class="row"><span class="label">Address:</span><span class="field"></span></div>
  <div class="row"><span class="label">DOB:</span><span class="field w120"></span><span class="label">Email Address:</span><span class="field"></span></div>
  <div class="row"><span class="label">Phone Number(s): Mobile:</span><span class="field"></span><span class="label">Work:</span><span class="field"></span><span class="label">Home:</span><span class="field"></span></div>
  <div class="row"><span class="label">Emergency Contact Person: Name:</span><span class="field"></span><span class="label">Relationship:</span><span class="field"></span></div>
  <div class="row"><span class="label">Phone number:</span><span class="field"></span></div>

  <div class="section-band">General Practitioner:</div>
  <div class="row"><span class="label">Name:</span><span class="field"></span><span class="label">Phone Number:</span><span class="field"></span></div>
  <div class="row"><span class="label">Practice Name:</span><span class="field"></span><span class="label">Referred by:</span><span class="field"></span></div>
  <div class="row"><span class="label">Do you have a health fund with dental cover? Yes<i class="box"></i> or No<i class="box"></i> If so, what is the name of the fund?</span><span class="field"></span></div>
  <div class="row"><span class="label">Fund Number:</span><span class="field"></span><span class="label">Priority Number on card: 0<i class="box"></i> 1<i class="box"></i> 2<i class="box"></i> 3<i class="box"></i> 4<i class="box"></i> 5<i class="box"></i></span></div>
  <div class="row"><span class="label">Occupation:</span><span class="field"></span></div>

  <div class="section-band">Please indicate if you are allergic to any of the following:</div>
  <div class="check-grid allergy">
    <span>Aspirin<i class="box"></i></span><span>Codeine<i class="box"></i></span><span>Penicillin<i class="box"></i></span><span>Sulfites<i class="box"></i></span>
    <span>Latex<i class="box"></i></span><span>Local Anaesthetic<i class="box"></i></span><span>Lactose<i class="box"></i></span><span>Nickel<i class="box"></i></span>
  </div>
  <div class="row"><span class="label">Other:</span><span class="field"></span></div>

  <div class="section-band">Are you currently taking, or have ever taken, any of the following medication?</div>
  <div class="check-grid meds">
    <span>Asthma inhaler<i class="box"></i></span><span>Anti-epileptics<i class="box"></i></span><span>Anti-depressants<i class="box"></i></span><span>Blood Pressure<i class="box"></i></span><span>Blood Thinners<i class="box"></i></span><span>Bisphosphonates<i class="box"></i></span>
    <span>Chemotherapy<i class="box"></i></span><span>Insulin<i class="box"></i></span><span>Immunosuppressants<i class="box"></i></span><span>Steroids<i class="box"></i></span><span>Oral Contraceptive<i class="box"></i></span><span>Other<i class="box"></i></span>
  </div>

  <div class="section-band">Please specify medication name, dose, and frequency where possible:</div>
  <div class="write-line"></div>
  <div class="write-line"></div>
  <div class="write-line"></div>

  <div class="question"><span>Do you require antibiotic cover?</span><span class="answers"><span>Yes<i class="box"></i></span><span>No<i class="box"></i></span></span></div>
  <div class="question"><span>Have you had a joint replacement?</span><span class="answers"><span>Yes<i class="box"></i></span><span>No<i class="box"></i></span></span></div>
  <div class="question"><span>Women: Are you pregnant? &nbsp; Yes<i class="box"></i> &nbsp; No<i class="box"></i> &nbsp; Possible<i class="box"></i> &nbsp; or &nbsp; Breast Feeding?</span><span class="answers"><span>Yes<i class="box"></i></span><span>No<i class="box"></i></span></span></div>

  <div class="turnover">Please Turnover</div>
</main>
</body>
</html>
```